4th Generation Family Business Needs a New Card Design!

We are a family owned 4th Generation company. We are based in the Sydney, Australia area and we are desperately in need of a more modern and classy card. We are monumental masons who design, supply & erect lasting memorials throughout cemeteries in Sydney. Our customers are normally in a period of grieving. I have attached logo files that will need to be implemented on the card. Company was established 1935. Australian Owned and Operated. Card needs to be designed to PIXO.com specification.

Target Market(s)

Our target market is based upon people that a grieving for family members that have passed away. We also deal with alot of companies that own and operate cemeteries.

Industry/Entity Type

Business

Contact Information for Business Card

Simon Harcourt, Operations Manager, 0417293086, simon@harcourtmemorials.com.au
Lewis Harcourt, Director, 0491630572, lewis@harcourtmemorials.com.au
Phone # 02 9561 3048
Website: www.harcourtmemorials.com.au
Address: Suite 17, 8 Palfrey Lane, West Carlow, Sydney NSW 2156

Font styles to use
Serif
Decorative
Script

Requirements
Must have
• Would like to see the logo nicely implemented with a modern design. Embossed lettering would be a nice additive.

```html
<!DOCTYPE html>
<html lang="en">
<head>
<meta charset="utf-8">
<title>Harcourt Memorials – Business Card</title>
<link rel="stylesheet" href="https://fonts.googleapis.com/css2?family=Cinzel:wght@400;600&family=Tinos&display=swap">
<style>
  :root {
    --page: #e4e4e4;
    --card-dark: #0b0c0e;
    --card-light: #f7f7f7;
    --gold: #d6b023;
    --gold-deep: #b8941a;
    --ink: #1b1b1b;
    --ink-soft: #2c2c2c;
    --white: #ffffff;
  }
  * { box-sizing: border-box; margin: 0; padding: 0; }
  html, body {
    width: 1200px; height: 576px; overflow: hidden;
    background: var(--page);
  }
  .canvas { position: relative; width: 1200px; height: 576px; }

  .card {
    position: absolute; top: 138px; width: 484px; height: 294px;
    overflow: hidden;
  }
  .card__band {
    position: absolute; left: 0; right: 0; bottom: 0; height: 10px;
    background: linear-gradient(180deg, var(--gold) 0%, var(--gold-deep) 100%);
  }

  /* Front */
  .card--front {
    left: 81px;
    background:
      radial-gradient(ellipse 120px 300px at 190px 120px, rgba(255,255,255,0.16), rgba(255,255,255,0) 70%),
      var(--card-dark);
  }
  .brand {
    font-family: "Cinzel", serif; font-weight: 400;
    text-align: center; text-transform: uppercase; line-height: 1;
  }
  .card--front .brand {
    position: absolute; left: 0; right: 0; top: 104px; color: var(--white);
  }
  .brand__main { display: block; font-size: 40px; letter-spacing: 1px; }
  .brand__sub { display: block; font-size: 17px; letter-spacing: 2px; margin-top: 8px; }

  /* Back */
  .card--back { left: 602px; background: var(--card-light); }
  .card--back .brand {
    position: absolute; left: 20px; width: 200px; top: 78px; color: var(--ink);
  }
  .card--back .brand__main { font-size: 30px; }
  .card--back .brand__sub { font-size: 13px; margin-top: 6px; }

  .person {
    position: absolute; right: 26px; top: 38px; text-align: right; color: var(--ink);
  }
  .person__name {
    font-family: "Cinzel", serif; font-weight: 600; font-size: 19px; letter-spacing: 0.5px;
  }
  .person__role {
    font-family: "Tinos", serif; font-size: 12px; margin-top: 2px;
  }

  .contacts {
    position: absolute; left: 25px; top: 174px; list-style: none;
    font-family: "Tinos", serif; font-size: 13px; color: var(--ink-soft);
  }
  .contacts li { display: flex; align-items: center; height: 17.5px; }
  .contacts svg { width: 10px; height: 10px; margin-right: 12px; fill: var(--gold); }
  .address {
    position: absolute; left: 25px; top: 246px;
    font-family: "Tinos", serif; font-size: 13px; color: var(--ink-soft);
  }
</style>
</head>
<body>
<main class="canvas">

  <section class="card card--front" aria-label="Card front">
    <div class="brand">
      <span class="brand__main">Harcourt</span>
      <span class="brand__sub">Memorials</span>
    </div>
    <div class="card__band"></div>
  </section>

  <section class="card card--back" aria-label="Card back">
    <div class="brand">
      <span class="brand__main">Harcourt</span>
      <span class="brand__sub">Memorials</span>
    </div>

    <div class="person">
      <p class="person__name">Simon Harcourt</p>
      <p class="person__role">Operations Manager</p>
    </div>

    <ul class="contacts">
      <li>
        <svg viewBox="0 0 10 10" aria-hidden="true"><path d="M2 0.5 L3.8 2.6 L2.9 3.6 Q4 5.9 6.4 7.1 L7.4 6.2 L9.5 8 L8.3 9.5 Q2.5 8.5 0.5 1.7 Z"/></svg>
        0491630572
      </li>
      <li>
        <svg viewBox="0 0 10 10" aria-hidden="true"><path d="M0.5 3 Q5 0 9.5 3 L9.5 4.2 L7.4 4.2 L7.2 3.3 Q5 2.6 2.8 3.3 L2.6 4.2 L0.5 4.2 Z M2.5 5 L7.5 5 L9 9.3 L1 9.3 Z"/></svg>
        02 9561 3048
      </li>
      <li>
        <svg viewBox="0 0 10 10" aria-hidden="true"><path d="M0.5 2 L9.5 2 L5 5.6 Z M0.5 3 L5 6.7 L9.5 3 L9.5 8.5 L0.5 8.5 Z"/></svg>
        lewis@harcourtmemorials.com.au
      </li>
      <li>
        <svg viewBox="0 0 10 10" aria-hidden="true"><circle cx="5" cy="5" r="4.5"/><path d="M0.5 5 H9.5 M5 0.5 V9.5 M5 0.5 Q2 5 5 9.5 M5 0.5 Q8 5 5 9.5" stroke="#f7f7f7" stroke-width="0.6" fill="none"/></svg>
        www.harcourtmemorials.com.au
      </li>
    </ul>

    <p class="address">Suite 17, 8 Palfrey Lane, West Carlow, Sydney NSW 2156</p>

    <div class="card__band"></div>
  </section>

</main>
</body>
</html>
```